Lakeshore Grain Corporate Powerpoint Template

We need a standardized corporate PowerPoint template that can be used for employees to create presentations with for events, meetings, and trainings. Our logo is blue, red, and white. I would like to feature the logo on each page and I visualize the "title page" to be navy blue based and "scream" Lakeshore Grain Company. I do not want the slide pages they use for content to be too busy, but still visually pleasing.

```html
<!DOCTYPE html>
<html lang="en">
<head>
<meta charset="utf-8">
<title>Lakeshore Grain – Corporate Presentation Template</title>
<link rel="stylesheet" href="https://fonts.googleapis.com/css2?family=Open+Sans:ital,wght@0,400;0,600;0,700;1,700&display=swap">
<style>
:root{
  --navy:#2b4ba3;
  --navy-dark:#1f3a85;
  --red:#d7263d;
  --ink:#333333;
  --body:#5a5a5a;
  --grey:#8a8f96;
  --light:#e8ecf7;
  --page:#ffffff;
}
*{box-sizing:border-box;margin:0;padding:0}
html,body{width:1200px;height:1200px;overflow:hidden;background:var(--page)}
.canvas{position:relative;width:1200px;height:1200px;font-family:'Open Sans',sans-serif;color:var(--ink)}
.slide{position:absolute;width:195px;height:110px;background:#fff;box-shadow:0 2px 6px rgba(0,0,0,.28);overflow:hidden}
.abs{position:absolute}
.blue{background:var(--navy)}
.red{background:var(--red)}
.logo{position:absolute;left:10px;top:5px;display:flex;align-items:center;gap:1.5px;font-size:3.2px;font-weight:700;color:var(--navy);white-space:nowrap}
.logo i{display:block;width:3.2px;height:3.2px;background:var(--red)}
.url{position:absolute;font-size:2.3px;letter-spacing:.3px;color:var(--navy);font-weight:600}
.foot{position:absolute;left:10px;right:8px;bottom:3px;display:flex;justify-content:space-between;font-size:2px;color:var(--navy);font-weight:700}
.foot span:last-child{letter-spacing:.3px}
.foot.light span:first-child{color:var(--light)}
.title{position:absolute;font-size:7px;line-height:1.15;color:var(--ink)}
.title b{color:var(--navy);font-weight:700;display:block}
.title.inline b{display:inline}
.title.center{text-align:center;left:0;right:0}
.title.white,.title.white b{color:#fff}
.body{font-size:2.3px;line-height:1.45;color:var(--body)}
.body.sm{font-size:2px}
.body.white{color:var(--light)}
.body strong{color:var(--navy);font-weight:700}
.body.white strong,.body.white b{color:#fff}
.ph{position:absolute}
.ph.field{background:linear-gradient(180deg,#5f8fd0 0%,#a9c8e4 38%,#4a8a3a 55%,#23511f 100%)}
.ph.sunset{background:linear-gradient(180deg,#f0b25a 0%,#d2692b 45%,#3b2a1c 72%,#1f1710 100%)}
.ph.beets{background:radial-gradient(circle at 40% 35%,#cfab7f,#8a6640 65%,#5c4228)}
.ph.plant{background:linear-gradient(135deg,#c3ccd6,#5a6571 55%,#8f9ba8)}
.ph.sepia{background:linear-gradient(180deg,#ddd1bc,#a6957a 60%,#6e604c)}
.ph.portrait{background:linear-gradient(180deg,#cfd8e0,#6a7482 55%,#2b2f3a)}
.ph.product{background:linear-gradient(135deg,#7aa35a 0%,#d42a3a 45%,#a51826)}
.ph.round{border-radius:50%}
.cover-logo{position:absolute;display:flex;align-items:center;justify-content:center;gap:2px;color:#fff;font-size:6px;font-weight:700;white-space:nowrap}
.cover-logo i{display:block;width:5px;height:5px;background:var(--red)}
.cover-name{position:absolute;color:#fff;text-align:center;font-size:4.6px;font-weight:700;line-height:1.1}
.cover-tag{position:absolute;color:var(--light);text-align:center;font-size:4px;line-height:1.1}
.presenter{position:absolute;left:20px;bottom:8px;font-size:2.4px;line-height:1.5;color:var(--navy);font-weight:700}
.presenter .date{color:var(--ink);font-weight:400}
.presenter i{display:inline-block;width:8px;height:.6px;background:var(--red);vertical-align:middle;margin-left:2px}
.bul{display:flex;gap:2px;align-items:flex-start;margin-bottom:3px}
.bul i{flex:none;width:3px;height:3px;border-radius:50%;background:var(--navy);margin-top:.4px}
.bul i.r{background:var(--red)}
.bul i.o{background:none;border:.4px solid var(--navy)}
.num{font-size:2.5px;font-weight:700;color:var(--navy)}
.card{position:absolute;background:var(--navy);color:#fff;text-align:center;font-size:2.5px;font-weight:700;line-height:1.2}
.card small{display:block;font-weight:400;font-size:1.9px;margin-top:.5px}
.year{font-size:5.5px;color:var(--red);font-weight:700}
.tl-col{position:absolute;width:40px}
.ring-lbl{font-size:2.4px;font-weight:700;text-align:center;color:var(--ink)}
.cols3{display:grid;grid-template-columns:repeat(3,1fr);gap:4px}
.phase{display:flex;border-bottom:.3px solid #999;font-size:2.1px}
.phase span{padding:.5px 2px}
.phase span:first-child{color:#fff;width:48px;font-weight:700}
.proc{padding:3px;color:#fff;font-size:2.2px;line-height:1.45}
.proc b{display:block;font-size:2.6px;margin-bottom:1px}
</style>
</head>
<body>
<div class="canvas">

<!-- Row 1 -->
<section class="slide" style="left:88px;top:32px">
  <div class="abs blue" style="left:90px;top:0;width:105px;height:110px"></div>
  <div class="url" style="left:21px;top:8px">www.lakeshoregrain.com</div>
  <div class="ph field" role="img" aria-label="Harvester working in a green beet field" style="left:7px;top:21px;width:108px;height:66px"></div>
  <div class="cover-logo" style="left:116px;top:34px;width:78px"><i></i>Lakeshore Grain</div>
  <div class="cover-name" style="left:118px;top:58px;width:74px">LAKESHORE GRAIN<br>COMPANY</div>
  <div class="cover-tag" style="left:118px;top:70px;width:74px">Growing Good Since<br>1906</div>
  <div class="presenter">Presented by: Daniel R. Morrow<br>November 2024 <i></i></div>
</section>

<section class="slide" style="left:367px;top:32px">
  <div class="abs blue" style="left:114px;top:0;width:81px;height:110px"></div>
  <div class="url" style="left:21px;top:8px">www.lakeshoregrain.com</div>
  <div class="ph field" role="img" aria-label="Hand holding a fresh beet over a field with a welcome greeting" style="left:2px;top:19px;width:134px;height:67px"></div>
  <div class="cover-logo" style="left:136px;top:30px;width:58px;font-size:4.6px"><i style="width:4px;height:4px"></i>Lakeshore Grain</div>
  <div class="cover-name" style="left:136px;top:54px;width:57px;font-size:4px">LAKESHORE GRAIN<br>COMPANY</div>
  <div class="cover-tag" style="left:136px;top:65px;width:57px;font-size:3.5px">Growing Good Since<br>1906</div>
  <div class="presenter" style="left:21px">Presented by: Daniel R. Morrow<br><span class="date">November 2024</span></div>
</section>

<section class="slide" style="left:646px;top:32px">
  <div class="abs blue" style="left:114px;top:0;width:81px;height:110px"></div>
  <div class="url" style="left:21px;top:8px">www.lakeshoregrain.com</div>
  <div class="ph sunset" role="img" aria-label="Harvest machinery in a field at sunset" style="left:2px;top:19px;width:134px;height:67px"></div>
  <div class="cover-logo" style="left:136px;top:30px;width:58px;font-size:4.6px"><i style="width:4px;height:4px"></i>Lakeshore Grain</div>
  <div class="cover-name" style="left:136px;top:54px;width:57px;font-size:4px">LAKESHORE GRAIN<br>COMPANY</div>
  <div class="cover-tag" style="left:136px;top:65px;width:57px;font-size:3.5px">Growing Good Since<br>1906</div>
  <div class="presenter" style="left:21px">Presented by: Daniel R. Morrow<br><span class="date">November 2024</span></div>
</section>

<section class="slide" style="left:924px;top:32px">
  <div class="logo"><i></i>Lakeshore Grain</div>
  <div class="title inline" style="left:14px;top:22px;font-size:7px">Today, <b>Agenda</b></div>
  <div class="abs" style="left:0;top:38px;width:195px;height:72px;background:linear-gradient(180deg,#2b4ba3,#243f8c)"></div>
  <div class="abs body white sm" style="left:14px;top:56px;width:170px;display:grid;grid-template-columns:repeat(5,1fr);gap:4px">
    <div>9:00 – 9:30<br><b>WELCOME</b><br>Opening words and goals.</div>
    <div>9:30 – 10:30<br><b>ABOUT</b><br>Our story and our people.</div>
    <div>11:30 – 12:00<br><b>BREAK</b><br>Coffee and time to chat.</div>
    <div>13:00 – 14:00<br><b>CASE STUDIES</b><br>Results from our farms.</div>
    <div>14:00 – 15:00<br><b>CLOSING</b><br>Questions and next steps.</div>
  </div>
  <div class="url" style="left:14px;top:100px;color:var(--light);font-size:2px">www.lakeshoregrain.com</div>
</section>

<!-- Row 2 -->
<section class="slide" style="left:88px;top:162px">
  <div class="ph portrait" role="img" aria-label="Portrait of the company president in an office" style="left:5px;top:5px;width:58px;height:98px"></div>
  <div class="abs blue" style="left:29px;top:83px;width:48px;height:18px"></div>
  <div class="abs" style="left:32px;top:86px;font-size:2.5px;font-weight:700;color:#fff;line-height:1.4">Daniel R. Morrow<br><span style="font-weight:400;font-size:2.1px">President and CEO</span></div>
  <div class="title" style="left:98px;top:16px">Welcome<b>Message</b></div>
  <div class="abs body" style="left:98px;top:35px;width:84px">Thank you for joining us today. For more than a century our growers, workers and partners have built a company that turns the harvest of this region into products families trust. This meeting is a chance to share where we stand, what we have learned and where we plan to go next. We are proud of the work done in our fields and plants, and grateful for the people who make it possible every single season.</div>
  <div class="foot" style="left:120px"><span></span><span>Growing Good Since 1906</span></div>
</section>

<section class="slide" style="left:367px;top:162px">
  <div class="logo"><i></i>Lakeshore Grain</div>
  <div class="title inline" style="left:11px;top:18px">About <b>Us</b></div>
  <div class="abs body" style="left:11px;top:30px;width:66px">Lakeshore Grain is a grower-owned company that has worked the land of this region since 1906. Our farms, plants and teams work side by side to turn each harvest into pure, natural products. We value care for the soil, safe work and honest trade with every partner we serve, season after season.</div>
  <div class="ph sepia" role="img" aria-label="Historic photograph of an early processing factory" style="left:82px;top:20px;width:113px;height:70px"></div>
  <div class="abs blue" style="left:93px;top:90px;width:27px;height:20px"></div>
  <div class="foot"><span>www.lakeshoregrain.com</span><span>Growing Good Since 1906</span></div>
</section>

<section class="slide" style="left:646px;top:162px">
  <div class="logo"><i></i>Lakeshore Grain</div>
  <div class="abs blue" style="left:43px;top:15px;width:134px;height:78px"></div>
  <div class="ph sepia" role="img" aria-label="Historic crowd outside the first factory" style="left:18px;top:28px;width:42px;height:25px"></div>
  <div class="ph sepia" role="img" aria-label="Historic view of the factory yard" style="left:18px;top:57px;width:42px;height:25px"></div>
  <div class="title white inline" style="left:88px;top:24px;font-size:7px">Our <b>History</b></div>
  <div class="abs body white" style="left:88px;top:36px;width:82px">Our first plant opened its doors in 1906 with a small group of local growers. Over the decades the company grew, merged with neighbours and moved to modern methods, while keeping its roots in the same fields. Today thousands of acres and hundreds of families carry that story forward.</div>
  <div class="foot"><span>www.lakeshoregrain.com</span><span>Growing Good Since 1906</span></div>
</section>

<section class="slide" style="left:924px;top:162px">
  <div class="logo"><i></i>Lakeshore Grain</div>
  <div class="abs blue" style="left:61px;top:30px;width:23px;height:80px"></div>
  <div class="ph plant" role="img" aria-label="Factory exterior" style="left:22px;top:18px;width:40px;height:36px"></div>
  <div class="ph plant" role="img" aria-label="Processing equipment" style="left:9px;top:54px;width:44px;height:36px"></div>
  <div class="ph plant" role="img" aria-label="Plant interior" style="left:62px;top:54px;width:26px;height:36px"></div>
  <div class="title" style="left:104px;top:18px;font-size:6.6px">Portfolio Slide<b>title goes here</b></div>
  <div class="abs body" style="left:104px;top:37px;width:82px">• A short note about this project, the team behind it and the result it delivered.<br>• A second point that adds detail on the scale, the timing or the lesson learned.<br>• A third point to close the story with a clear next step for the group.</div>
  <div class="foot"><span>www.lakeshoregrain.com</span><span>Growing Good Since 1906</span></div>
</section>

<!-- Row 3 -->
<section class="slide" style="left:88px;top:291px">
  <div class="logo"><i></i>Lakeshore Grain</div>
  <div class="title" style="left:12px;top:22px;font-size:6.6px">Two bullet point<b>Title Slide Here</b></div>
  <div class="abs body" style="left:12px;top:42px;width:70px"><span class="num">01 // Short heading text</span><br>A short line of text to explain the first point clearly.<br><br><span class="num">02 // Short heading text</span><br>A short line of text to explain the second point clearly.</div>
  <div class="abs blue" style="left:116px;top:0;width:40px;height:110px"></div>
  <div class="ph plant" role="img" aria-label="Factory silos" style="left:99px;top:25px;width:35px;height:33px"></div>
  <div class="ph plant" role="img" aria-label="Processing tanks" style="left:136px;top:18px;width:43px;height:40px"></div>
  <div class="ph plant" role="img" aria-label="Worker in the plant" style="left:118px;top:60px;width:40px;height:38px"></div>
  <div class="foot"><span>www.lakeshoregrain.com</span><span>Growing Good Since 1906</span></div>
</section>

<section class="slide" style="left:367px;top:291px">
  <div class="logo"><i></i>Lakeshore Grain</div>
  <div class="ph beets round" role="img" aria-label="Pile of harvested beets" style="left:-10px;top:40px;width:70px;height:70px"></div>
  <div class="ph field round" role="img" aria-label="Farm field" style="left:45px;top:45px;width:40px;height:40px"></div>
  <div class="ph field round" role="img" aria-label="Farm building" style="left:22px;top:25px;width:24px;height:24px"></div>
  <div class="title" style="left:96px;top:11px;font-size:6.6px">Three bullet point<b>Title Slide Here</b></div>
  <div class="abs body" style="left:96px;top:30px;width:88px"><span class="num">01 // Short heading text</span><br>A short line of text for the first point.<br><br><span class="num">02 // Short heading text</span><br>A short line of text for the second point.<br><br><span class="num">03 // Short heading text</span><br>A short line of text for the third point.</div>
  <div class="foot"><span></span><span>Growing Good Since 1906</span></div>
</section>

<section class="slide" style="left:646px;top:291px">
  <div class="logo"><i></i>Lakeshore Grain</div>
  <div class="title inline center" style="top:6px;font-size:6.4px">Executive <b>Leadership Team</b></div>
  <div class="card" style="left:10px;top:20px;width:32px;height:70px"><div class="ph portrait" role="img" aria-label="Executive portrait" style="left:3px;top:3px;width:26px;height:39px"></div><div style="margin-top:46px">Alan<br>Brooks<small>Chief Officer</small></div></div>
  <div class="card" style="left:45px;top:20px;width:32px;height:70px"><div class="ph portrait" role="img" aria-label="Executive portrait" style="left:3px;top:3px;width:26px;height:39px"></div><div style="margin-top:46px">Alan<br>Brooks<small>Chief Officer</small></div></div>
  <div class="card" style="left:81px;top:20px;width:32px;height:70px"><div class="ph portrait" role="img" aria-label="Executive portrait" style="left:3px;top:3px;width:26px;height:39px"></div><div style="margin-top:46px">Alan<br>Brooks<small>Chief Officer</small></div></div>
  <div class="card" style="left:116px;top:20px;width:32px;height:70px"><div class="ph portrait" role="img" aria-label="Executive portrait" style="left:3px;top:3px;width:26px;height:39px"></div><div style="margin-top:46px">Alan<br>Brooks<small>Chief Officer</small></div></div>
  <div class="card" style="left:152px;top:20px;width:32px;height:70px"><div class="ph portrait" role="img" aria-label="Executive portrait" style="left:3px;top:3px;width:26px;height:39px"></div><div style="margin-top:46px">Alan<br>Brooks<small>Chief Officer</small></div></div>
  <div class="foot"><span>www.lakeshoregrain.com</span><span>Growing Good Since 1906</span></div>
</section>

<section class="slide" style="left:924px;top:291px">
  <div class="logo"><i></i>Lakeshore Grain</div>
  <div class="title" style="left:11px;top:22px;font-size:6.6px">About Our<b>Products</b></div>
  <div class="abs body" style="left:11px;top:40px;width:80px">• Pure granulated and powdered products packed fresh in our own plants.<br>• Bulk supply for bakers, food makers and local shops across the region.<br>• Every bag is traced back to the farms that grew it.</div>
  <div class="ph product" role="img" aria-label="Stack of red product bags on a green field" style="left:93px;top:0;width:102px;height:100px;border-bottom-left-radius:60px 90px"></div>
  <div class="foot"><span>www.lakeshoregrain.com</span><span>Growing Good Since 1906</span></div>
</section>

<!-- Row 4 -->
<section class="slide" style="left:88px;top:420px">
  <div class="logo"><i></i>Lakeshore Grain</div>
  <div class="title" style="left:12px;top:20px;font-size:6.6px">About Our<b>Operations</b></div>
  <div class="abs body" style="left:12px;top:38px;width:60px">Short intro line for this topic.</div>
  <div class="abs body" style="left:12px;top:50px;width:92px"><div class="bul"><i></i><span><strong>Short heading text</strong><br>A short line to explain this point.</span></div><div class="bul"><i class="r"></i><span><strong>Short heading text</strong><br>A short line to explain this point.</span></div></div>
  <div class="ph field" role="img" aria-label="Harvester in a field" style="left:113px;top:0;width:82px;height:110px"></div>
  <div class="foot" style="right:90px"><span>www.lakeshoregrain.com</span><span></span></div>
</section>

<section class="slide" style="left:367px;top:420px">
  <div class="logo"><i></i>Lakeshore Grain</div>
  <div class="abs blue" style="left:0;top:43px;width:195px;height:24px"></div>
  <div class="ph field round" role="img" aria-label="Rows of crops" style="left:12px;top:16px;width:60px;height:60px"></div>
  <div class="ph beets round" role="img" aria-label="Harvested beets" style="left:120px;top:16px;width:60px;height:60px"></div>
  <div class="abs" role="img" aria-label="Farm machinery in a field" style="left:61px;top:16px;width:68px;height:68px;border-radius:50%;background:rgba(31,58,133,.88)"></div>
  <div class="abs" style="left:61px;top:30px;width:68px;text-align:center;color:#fff;font-size:4.4px;line-height:1.15">Amazing<br><b>Farming Areas</b></div>
  <div class="abs body white sm" style="left:69px;top:43px;width:52px;text-align:center">A short line about the fields, the soil and the growers who care for them.</div>
  <div class="foot"><span>www.lakeshoregrain.com</span><span>Growing Good Since 1906</span></div>
</section>

<section class="slide" style="left:646px;top:420px">
  <div class="logo"><i></i>Lakeshore Grain</div>
  <div class="abs blue" style="left:30px;top:10px;width:33px;height:100px"></div>
  <div class="ph" role="img" aria-label="Strawberry dipped in cream" style="left:22px;top:20px;width:33px;height:32px;background:linear-gradient(135deg,#f4f1ec,#c4333f 60%,#8f1e28)"></div>
  <div class="ph field" role="img" aria-label="Crop field with harvester" style="left:22px;top:56px;width:33px;height:30px"></div>
  <div class="title" style="left:95px;top:18px;font-size:6.4px">About Harvest<b>Operations</b></div>
  <div class="abs body" style="left:95px;top:35px;width:86px"><strong>Short heading text</strong> with a short line to open this topic.</div>
  <div class="abs body" style="left:92px;top:52px;width:92px"><div class="bul"><i></i><span><strong>Short heading text</strong><br>A short line to explain this point.</span></div><div class="bul"><i class="r"></i><span><strong>Short heading text</strong><br>A short line to explain this point.</span></div></div>
  <div class="foot"><span>www.lakeshoregrain.com</span><span>Growing Good Since 1906</span></div>
</section>

<section class="slide" style="left:924px;top:420px">
  <div class="logo"><i></i>Lakeshore Grain</div>
  <div class="abs blue" style="left:81px;top:0;width:114px;height:60px"></div>
  <div class="title" style="left:25px;top:20px;font-size:6.2px">About Harvest<b>Operations</b></div>
  <div class="abs body sm" style="left:25px;top:36px;width:52px">Short intro line for this topic.</div>
  <div class="ph sunset" role="img" aria-label="Harvest at sunset" style="left:85px;top:18px;width:94px;height:32px"></div>
  <div class="ph field" role="img" aria-label="Green field" style="left:23px;top:55px;width:38px;height:33px"></div>
  <div class="ph beets" role="img" aria-label="Beet pile" style="left:63px;top:55px;width:38px;height:33px"></div>
  <div class="abs body sm" style="left:110px;top:57px;width:74px"><div class="bul"><span><strong>✓ Short heading</strong> a short line.</span></div><div class="bul"><span><strong>✓ Short heading</strong> a short line.</span></div><div class="bul"><span><strong>✓ Short heading</strong> a short line.</span></div></div>
  <div class="foot"><span>www.lakeshoregrain.com</span><span>Growing Good Since 1906</span></div>
</section>

<!-- Row 5 -->
<section class="slide" style="left:88px;top:549px">
  <div class="logo"><i></i>Lakeshore Grain</div>
  <div class="abs blue" style="left:0;top:18px;width:195px;height:38px"></div>
  <div class="ph sunset" role="img" aria-label="Harvest machinery at sunset" style="left:32px;top:18px;width:163px;height:37px"></div>
  <div class="abs" style="left:32px;top:18px;width:52px;height:30px;background:rgba(43,75,163,.88)"></div>
  <div class="abs" style="left:35px;top:23px;font-size:6.4px;font-weight:700;color:#fff">+ 10.78 %</div>
  <div class="abs body white sm" style="left:35px;top:34px;width:46px">Growth in yield over last season.</div>
  <div class="title" style="left:14px;top:60px;font-size:5.8px">About Harvest<b>Operations</b></div>
  <div class="abs body sm cols3" style="left:64px;top:59px;width:122px">
    <div><strong>✓ Short heading</strong><br>A short line to explain this point in brief.</div>
    <div><strong>✓ Short heading</strong><br>A short line to explain this point in brief.</div>
    <div><strong>✓ Short heading</strong><br>A short line to explain this point in brief.</div>
  </div>
  <div class="foot"><span>www.lakeshoregrain.com</span><span>Growing Good Since 1906</span></div>
</section>

<section class="slide" style="left:367px;top:549px">
  <div class="logo"><i></i>Lakeshore Grain</div>
  <div class="abs blue" style="left:17px;top:30px;width:60px;height:80px"></div>
  <div class="ph plant" role="img" aria-label="Plant silo" style="left:10px;top:38px;width:18px;height:30px"></div>
  <div class="ph beets" role="img" aria-label="Beets on a conveyor" style="left:12px;top:50px;width:38px;height:60px"></div>
  <div class="ph plant" role="img" aria-label="Lab worker inspecting a sample" style="left:58px;top:14px;width:38px;height:80px"></div>
  <div class="title" style="left:110px;top:24px;font-size:6.2px">About Our<b>Plant Process</b></div>
  <div class="abs body" style="left:110px;top:45px;width:76px"><div class="bul"><i class="o"></i><span><strong>Certified Land</strong><br>A short line about this step.</span></div><div class="bul" style="margin-top:4px"><i class="o"></i><span><strong>Tested Land</strong><br>A short line about this step.</span></div></div>
  <div class="foot"><span></span><span>Growing Good Since 1906</span></div>
</section>

<section class="slide" style="left:646px;top:549px">
  <div class="logo"><i></i>Lakeshore Grain</div>
  <div class="ph" role="img" aria-label="Worker inspecting green beet leaves" style="left:27px;top:19px;width:168px;height:64px;background:linear-gradient(135deg,#5f9a45,#2d6327 60%,#1d4619)"></div>
  <div class="abs blue" style="left:3px;top:36px;width:86px;height:53px"></div>
  <div class="title white" style="left:10px;top:41px;font-size:5.8px">Keeping On<b>High Quality</b></div>
  <div class="abs body white sm" style="left:10px;top:56px;width:75px"><b>Short heading text</b> and a short line about the checks we run on every load, from field to final pack.</div>
  <div class="abs red" style="left:65px;top:89px;width:24px;height:1px"></div>
  <div class="foot"><span>www.lakeshoregrain.com</span><span>Growing Good Since 1906</span></div>
</section>

<section class="slide" style="left:924px;top:549px">
  <div class="logo"><i></i>Lakeshore Grain</div>
  <div class="title inline center" style="top:16px;font-size:6.2px">About Our <b>Plant Process</b></div>
  <div class="abs body sm" style="left:0;right:0;top:26px;text-align:center">A short line to open this topic.</div>
  <div class="abs blue" style="left:0;top:35px;width:195px;height:32px"></div>
  <div class="ph plant" role="img" aria-label="Row of processing machinery" style="left:0;top:37px;width:195px;height:29px"></div>
  <div class="abs body sm cols3" style="left:20px;top:74px;width:160px;gap:6px">
    <div><strong>✓</strong> A short line about the first step.</div>
    <div><strong>✓</strong> A short line about the next step.</div>
    <div><strong>✓</strong> A short line about the final step.</div>
  </div>
  <div class="foot"><span>www.lakeshoregrain.com</span><span>Growing Good Since 1906</span></div>
</section>

<!-- Row 6 -->
<section class="slide" style="left:88px;top:678px">
  <div class="logo"><i></i>Lakeshore Grain</div>
  <div class="abs blue" style="left:0;top:35px;width:185px;height:60px"></div>
  <div class="ph plant" role="img" aria-label="Lab worker" style="left:56px;top:14px;width:40px;height:43px"></div>
  <div class="ph plant" role="img" aria-label="Processing tanks" style="left:98px;top:14px;width:40px;height:43px"></div>
  <div class="ph plant" role="img" aria-label="Packaging line" style="left:140px;top:14px;width:40px;height:43px"></div>
  <div class="title white" style="left:13px;top:40px;font-size:5.8px;font-weight:400">About<br>Our<b>Plant<br>Process</b></div>
  <div class="abs body white sm" style="left:13px;top:76px;width:36px">A short intro line.</div>
  <div class="abs body white sm cols3" style="left:56px;top:60px;width:126px;gap:3px">
    <div><b>✓ Short heading</b><br>A short line about this step.</div>
    <div><b>✓ Short heading</b><br>A short line about this step.</div>
    <div><b>✓ Short heading</b><br>A short line about this step.</div>
  </div>
  <div class="foot"><span>www.lakeshoregrain.com</span><span>Growing Good Since 1906</span></div>
</section>

<section class="slide" style="left:367px;top:678px">
  <div class="logo"><i></i>Lakeshore Grain</div>
  <div class="ph sepia" role="img" aria-label="Historic photo of field workers harvesting beets" style="left:14px;top:14px;width:82px;height:80px"></div>
  <div class="abs blue" style="left:83px;top:24px;width:112px;height:60px"></div>
  <div class="abs" style="left:87px;top:30px;width:103px;font-size:2.5px;line-height:1.4;color:#fff;font-weight:700;font-style:italic">Since our founding, more than a century ago, our growers have perfected the craft of turning the region's crops into pure, natural products.<br><br>Today, Lakeshore Grain is a leading regional processor, producing millions of pounds each year under the Harbor Crest brand.</div>
  <div class="foot"><span>www.lakeshoregrain.com</span><span>Growing Good Since 1906</span></div>
</section>

<section class="slide" style="left:646px;top:678px">
  <div class="logo"><i></i>Lakeshore Grain</div>
  <div class="ph field" role="img" aria-label="Wide field of young crops under a clear sky" style="left:10px;top:18px;width:185px;height:76px"></div>
  <div class="abs blue" style="left:10px;top:42px;width:70px;height:55px"></div>
  <div class="title white" style="left:17px;top:53px;font-size:5.8px;font-weight:400">Break Slide<b>Presentations</b></div>
  <div class="abs body white sm" style="left:17px;top:73px">Relax, we will be back soon.</div>
  <div class="abs red" style="left:66px;top:96px;width:14px;height:1px"></div>
  <div class="foot"><span>www.lakeshoregrain.com</span><span>Growing Good Since 1906</span></div>
</section>

<section class="slide" style="left:924px;top:678px">
  <div class="logo"><i></i>Lakeshore Grain</div>
  <div class="title inline center" style="top:17px;font-size:6.2px">More <b>About Our Production</b></div>
  <div class="abs body sm" style="left:0;right:0;top:27px;text-align:center">A short line to open this topic.</div>
  <div class="ph sunset" role="img" aria-label="Harvester at sunset" style="left:0;top:34px;width:195px;height:39px"></div>
  <div class="abs blue" style="left:0;top:34px;width:195px;height:39px;opacity:.35"></div>
  <div class="abs" style="left:15px;top:45px;width:19px;height:19px;border-radius:50%;background:var(--navy);border:1px solid #fff"></div>
  <svg class="abs" style="left:21.5px;top:48px" width="6" height="6" viewBox="0 0 6 6"><path d="M1 5 L5 1 M1 1 L5 5" stroke="#fff" stroke-width=".8"/></svg>
  <div class="abs" style="left:15px;top:57px;width:19px;text-align:center;font-size:1.9px;color:#fff">Agriculture</div>
  <div class="abs body sm" style="left:20px;right:20px;top:77px;text-align:center">A short summary of how our plants turn each harvest into finished goods, with care taken at every stage of the line.</div>
  <div class="foot"><span>www.lakeshoregrain.com</span><span>Growing Good Since 1906</span></div>
</section>

<!-- Row 7 -->
<section class="slide" style="left:88px;top:807px">
  <div class="logo"><i></i>Lakeshore Grain</div>
  <div class="abs blue" style="left:0;top:46px;width:195px;height:64px"></div>
  <div class="abs" style="left:99px;top:93px;width:96px;height:17px;background:#fff"></div>
  <div class="title" style="left:21px;top:26px;font-size:5.8px">Talking About Our<b>Production Numbers</b></div>
  <div class="abs body white sm" style="left:21px;top:52px;width:74px"><b>Short heading text</b> and a short line about this year's output.</div>
  <div class="abs" style="left:21px;top:70px;font-size:5.6px;font-weight:700;color:#fff">89.32%</div>
  <div class="abs" style="left:58px;top:70px;font-size:5.6px;font-weight:700;color:#fff">80.32%</div>
  <div class="abs body white sm" style="left:21px;top:79px">Plant use</div>
  <div class="abs body white sm" style="left:58px;top:79px">Field yield</div>
  <svg class="abs" style="left:100px;top:20px" width="95" height="72" viewBox="0 0 95 72" role="img" aria-label="Laptop showing a photo of the factory">
    <path d="M10 2 L95 2 L95 62 L4 62 Z" fill="#222"/>
    <rect x="13" y="5" width="82" height="54" fill="#8fa3bd"/>
    <path d="M0 62 L95 62 L95 70 L4 70 Z" fill="#bfc4ca"/>
  </svg>
  <div class="foot light"><span>www.lakeshoregrain.com</span><span>Growing Good Since 1906</span></div>
</section>

<section class="slide" style="left:367px;top:807px">
  <div class="logo"><i></i>Lakeshore Grain</div>
  <div class="title inline center" style="top:16px;font-size:6.2px">Data <b>Slide Title</b></div>
  <div class="abs body sm" style="left:0;right:0;top:26px;text-align:center">Chart Title</div>
  <svg class="abs" style="left:15px;top:32px" width="170" height="62" viewBox="0 0 170 62">
    <g stroke="#e4e4e4" stroke-width=".3"><line x1="8" y1="5" x2="168" y2="5"/><line x1="8" y1="15" x2="168" y2="15"/><line x1="8" y1="25" x2="168" y2="25"/><line x1="8" y1="35" x2="168" y2="35"/><line x1="8" y1="45" x2="168" y2="45"/><line x1="8" y1="55" x2="168" y2="55"/></g>
    <g font-family="Open Sans, sans-serif" font-size="2" fill="#777" text-anchor="end"><text x="6" y="6">5</text><text x="6" y="16">4</text><text x="6" y="26">3</text><text x="6" y="36">2</text><text x="6" y="46">1</text><text x="6" y="56">0</text></g>
    <g fill="#2b4ba3"><rect x="15" y="25" width="4" height="30"/><rect x="42" y="35" width="4" height="20"/><rect x="69" y="28" width="4" height="27"/><rect x="96" y="15" width="4" height="40"/><rect x="123" y="30" width="4" height="25"/><rect x="150" y="23" width="4" height="32"/></g>
    <g fill="#d7263d"><rect x="21" y="32" width="4" height="23"/><rect x="48" y="22" width="4" height="33"/><rect x="75" y="12" width="4" height="43"/><rect x="102" y="36" width="4" height="19"/><rect x="129" y="40" width="4" height="15"/><rect x="156" y="30" width="4" height="25"/></g>
    <polyline points="17,48 44,44 71,46 98,40 125,28 152,10" fill="none" stroke="#d7263d" stroke-width=".5"/>
  </svg>
  <div class="abs body sm" style="left:27px;right:10px;top:93px;display:flex;justify-content:space-between"><span>Category 1</span><span>Category 2</span><span>Category 3</span><span>Category 4</span><span>Category 5</span><span>Category 6</span></div>
  <div class="foot"><span>www.lakeshoregrain.com</span><span>Growing Good Since 1906</span></div>
</section>

<section class="slide" style="left:646px;top:807px">
  <div class="logo"><i></i>Lakeshore Grain</div>
  <div class="title inline center" style="top:16px;font-size:6.4px">Data Multiple <b>Pie Slide</b></div>
  <svg class="abs" style="left:15px;top:31px" width="170" height="32" viewBox="0 0 170 32">
    <g fill="none" stroke-width="2.2">
      <circle cx="20" cy="16" r="12" stroke="#e6e6e6"/><circle cx="20" cy="16" r="12" stroke="#d7263d" stroke-dasharray="37.7 75.4" transform="rotate(-90 20 16)"/>
      <circle cx="63" cy="16" r="12" stroke="#e6e6e6"/><circle cx="63" cy="16" r="12" stroke="#d7263d" stroke-dasharray="22.6 75.4" transform="rotate(-90 63 16)"/>
      <circle cx="107" cy="16" r="12" stroke="#e6e6e6"/><circle cx="107" cy="16" r="12" stroke="#d7263d" stroke-dasharray="7.5 75.4" transform="rotate(-90 107 16)"/>
      <circle cx="150" cy="16" r="12" stroke="#e6e6e6"/><circle cx="150" cy="16" r="12" stroke="#2b4ba3" stroke-dasharray="30.2 75.4" transform="rotate(-90 150 16)"/>
    </g>
    <g font-family="Open Sans, sans-serif" font-size="4.4" font-weight="700" fill="#333" text-anchor="middle"><text x="20" y="17.6">50%</text><text x="63" y="17.6">30%</text><text x="107" y="17.6">10%</text><text x="150" y="17.6">40%</text></g>
  </svg>
  <div class="abs" style="left:15px;top:67px;width:170px;display:grid;grid-template-columns:repeat(4,1fr);gap:6px">
    <div><div class="ring-lbl">Data title here</div><div class="body sm" style="text-align:center">A short line about this figure.</div></div>
    <div><div class="ring-lbl">Data title here</div><div class="body sm" style="text-align:center">A short line about this figure.</div></div>
    <div><div class="ring-lbl">Data title here</div><div class="body sm" style="text-align:center">A short line about this figure.</div></div>
    <div><div class="ring-lbl">Data title here</div><div class="body sm" style="text-align:center">A short line about this figure.</div></div>
  </div>
  <div class="foot"><span>www.lakeshoregrain.com</span><span>Growing Good Since 1906</span></div>
</section>

<section class="slide" style="left:924px;top:807px">
  <div class="logo"><i></i>Lakeshore Grain</div>
  <div class="title inline center" style="top:16px;font-size:6.4px">Data Multiple <b>Pie Slide #2</b></div>
  <svg class="abs" style="left:10px;top:30px" width="180" height="62" viewBox="0 0 180 62">
    <g fill="none" stroke-width="1.8">
      <circle cx="20" cy="14" r="10" stroke="#e6e6e6"/><circle cx="20" cy="14" r="10" stroke="#d7263d" stroke-dasharray="6.3 62.8" transform="rotate(-90 20 14)"/>
      <circle cx="87" cy="14" r="10" stroke="#e6e6e6"/><circle cx="87" cy="14" r="10" stroke="#2b4ba3" stroke-dasharray="56.5 62.8" transform="rotate(-90 87 14)"/>
      <circle cx="154" cy="14" r="10" stroke="#e6e6e6"/><circle cx="154" cy="14" r="10" stroke="#2b4ba3" stroke-dasharray="47.1 62.8" transform="rotate(-90 154 14)"/>
      <circle cx="53" cy="47" r="10" stroke="#e6e6e6"/><circle cx="53" cy="47" r="10" stroke="#2b4ba3" stroke-dasharray="22 62.8" transform="rotate(-90 53 47)"/>
      <circle cx="120" cy="47" r="10" stroke="#e6e6e6"/><circle cx="120" cy="47" r="10" stroke="#d7263d" stroke-dasharray="14.4 62.8" transform="rotate(-90 120 47)"/>
    </g>
    <g font-family="Open Sans, sans-serif" font-size="4" font-weight="700" fill="#333" text-anchor="middle"><text x="20" y="15.4">10%</text><text x="87" y="15.4">90%</text><text x="154" y="15.4">75%</text><text x="53" y="48.4">35%</text><text x="120" y="48.4">23%</text></g>
  </svg>
  <div class="abs ring-lbl" style="left:46px;top:33px;width:34px;font-size:2.1px">Data title here<div class="body sm" style="font-weight:400">A short line here.</div></div>
  <div class="abs ring-lbl" style="left:113px;top:33px;width:34px;font-size:2.1px">Data title here<div class="body sm" style="font-weight:400">A short line here.</div></div>
  <div class="abs ring-lbl" style="left:12px;top:57px;width:34px;font-size:2.1px">Data title here<div class="body sm" style="font-weight:400">A short line here.</div></div>
  <div class="abs ring-lbl" style="left:80px;top:57px;width:34px;font-size:2.1px">Data title here<div class="body sm" style="font-weight:400">A short line here.</div></div>
  <div class="abs ring-lbl" style="left:147px;top:57px;width:34px;font-size:2.1px">Data title here<div class="body sm" style="font-weight:400">A short line here.</div></div>
  <div class="foot"><span>www.lakeshoregrain.com</span><span>Growing Good Since 1906</span></div>
</section>

<!-- Row 8 -->
<section class="slide" style="left:88px;top:936px">
  <div class="logo"><i></i>Lakeshore Grain</div>
  <div class="title inline center" style="top:15px;font-size:6.4px">Timeline <b>Project</b></div>
  <div class="abs red" style="left:13px;top:29px;width:15px;height:10px;color:#fff;font-size:3.2px;text-align:center;line-height:10px">start</div>
  <div class="abs body sm" style="left:35px;top:28px;width:148px"><strong>Description</strong><br>A short overview of the project, its goal and the teams involved from the first step to the last.</div>
  <div class="abs" style="left:35px;top:51px;width:150px;height:.3px;background:#ccc"></div>
  <div class="tl-col" style="left:35px;top:53px"><div class="year">2017</div><div class="body sm">Your first milestone here. A short line about what was done.</div></div>
  <div class="tl-col" style="left:88px;top:53px"><div class="year">2019</div><div class="body sm">Your second milestone. A short line about what was done.</div></div>
  <div class="tl-col" style="left:141px;top:53px"><div class="year">2021</div><div class="body sm">Your third milestone. A short line about what was done.</div></div>
  <div class="foot"><span>www.lakeshoregrain.com</span><span>Growing Good Since 1906</span></div>
</section>

<section class="slide" style="left:367px;top:936px">
  <div class="logo"><i></i>Lakeshore Grain</div>
  <div class="title inline center" style="top:15px;font-size:6.4px">Timeline <b>Project</b></div>
  <div class="abs body sm" style="left:10px;top:27px;width:82px"><strong>Description</strong><br>A short overview of the first phase and its main goal.</div>
  <div class="abs body sm" style="left:100px;top:27px;width:82px"><strong>Description</strong><br>A short overview of the second phase and its main goal.</div>
  <div class="abs" style="left:10px;top:50px;width:175px;height:.3px;background:#ccc"></div>
  <div class="tl-col" style="left:10px;top:52px;width:38px"><div class="year">2022</div><div class="body sm">A short line about this milestone.</div></div>
  <div class="tl-col" style="left:55px;top:52px;width:38px"><div class="year">2023</div><div class="body sm">A short line about this milestone.</div></div>
  <div class="tl-col" style="left:100px;top:52px;width:38px"><div class="year">2024</div><div class="body sm">A short line about this milestone.</div></div>
  <div class="tl-col" style="left:145px;top:52px;width:38px"><div class="year">2025</div><div class="body sm">A short line about this milestone.</div></div>
  <div class="foot"><span>www.lakeshoregrain.com</span><span>Growing Good Since 1906</span></div>
</section>

<section class="slide" style="left:646px;top:936px">
  <div class="logo"><i></i>Lakeshore Grain</div>
  <div class="title inline center" style="top:15px;font-size:6.4px">Timeline <b>Project</b></div>
  <div class="abs body sm" style="left:13px;top:28px;width:145px"><strong>Description</strong><br>A short overview of the project, its goal and the teams involved from the first step to the last.</div>
  <div class="abs blue" style="left:166px;top:29px;width:15px;height:10px;color:#fff;font-size:3.2px;text-align:center;line-height:10px">Done</div>
  <div class="abs" style="left:10px;top:51px;width:150px;height:.3px;background:#ccc"></div>
  <div class="tl-col" style="left:12px;top:53px"><div class="year">2026</div><div class="body sm">Your next milestone here. A short line about the plan.</div></div>
  <div class="tl-col" style="left:65px;top:53px"><div class="year">2027</div><div class="body sm">Your next milestone here. A short line about the plan.</div></div>
  <div class="tl-col" style="left:118px;top:53px"><div class="year">2028</div><div class="body sm">Your next milestone here. A short line about the plan.</div></div>
  <div class="foot"><span>www.lakeshoregrain.com</span><span>Growing Good Since 1906</span></div>
</section>

<section class="slide" style="left:924px;top:936px">
  <div class="logo"><i></i>Lakeshore Grain</div>
  <div class="title inline center" style="top:16px;font-size:6.2px">One Column <b>Text Slide</b></div>
  <div class="abs body sm" style="left:14px;top:29px;width:168px">Use this slide for a longer message that needs room to breathe. Keep each paragraph to a single idea so the audience can follow along, and let the heading above carry the main point of the page. A short quote, a policy note or a summary of results all fit well here.<br><br>A second paragraph can add context, such as the reason behind a decision, the people involved or the next steps the team will take. Close with a clear action so everyone leaves the room knowing what comes next and who will lead it.</div>
  <div class="foot"><span>www.lakeshoregrain.com</span><span>Growing Good Since 1906</span></div>
</section>

<!-- Row 9 -->
<section class="slide" style="left:88px;top:1066px">
  <div class="logo"><i></i>Lakeshore Grain</div>
  <div class="title inline center" style="top:17px;font-size:6.2px">Overview <b>2 Column</b></div>
  <div class="abs body" style="left:14px;top:27px;width:168px"><strong>A short lead sentence for this page</strong> that sets up the two columns below.</div>
  <div class="abs body sm" style="left:14px;top:38px;width:80px"><span style="color:var(--navy);font-size:2.5px">What is this section?</span><br>A short paragraph that explains the first idea in plain words, with one or two facts to support it and a clear close for the reader.</div>
  <div class="abs body sm" style="left:102px;top:38px;width:80px"><span style="color:var(--navy);font-size:2.5px">Why do we use it?</span><br>A short paragraph that explains the second idea in plain words, with one or two facts to support it and a clear close for the reader.</div>
  <div class="foot"><span>www.lakeshoregrain.com</span><span>Growing Good Since 1906</span></div>
</section>

<section class="slide" style="left:367px;top:1066px">
  <div class="logo"><i></i>Lakeshore Grain</div>
  <div class="title inline center" style="top:15px;font-size:6.2px">Infographic <b>Slide</b></div>
  <div class="abs body sm" style="left:10px;top:27px;width:175px">
    <div class="phase"><span style="background:var(--navy)">Diagnosis phase</span><span>The problem</span></div>
    <div style="padding:1.5px 2px 2.5px">• Gather the data from each site.<br>• Define the issue and its cause.</div>
    <div class="phase"><span style="background:var(--red)">Experiment phase</span><span>Problem control</span></div>
    <div style="padding:1.5px 2px 2.5px">• Test a small fix on one line.<br>• Measure the result against the goal.</div>
    <div class="phase"><span style="background:var(--grey)">Resolution phase</span><span>Error control</span></div>
    <div style="padding:1.5px 2px 2.5px">• Roll the fix out to every plant.</div>
  </div>
  <div class="foot"><span>www.lakeshoregrain.com</span><span>Growing Good Since 1906</span></div>
</section>

<section class="slide" style="left:646px;top:1066px">
  <div class="logo"><i></i>Lakeshore Grain</div>
  <div class="title inline center" style="top:15px;font-size:6.2px">Infographic <b>Slide</b></div>
  <div class="abs" style="left:13px;top:28px;width:170px;height:64px;display:grid;grid-template-columns:repeat(4,1fr);gap:1.5px">
    <div class="proc" style="background:var(--grey)"><b>Process One</b>A short line about this first stage of the work.</div>
    <div class="proc" style="background:#3d6fc0"><b>Process Two</b>A short line about this second stage of the work.</div>
    <div class="proc" style="background:var(--navy)"><b>Process Three</b>A short line about this third stage of the work.</div>
    <div class="proc" style="background:var(--red)"><b>Process Four</b>A short line about this final stage of the work.</div>
  </div>
  <div class="foot"><span>www.lakeshoregrain.com</span><span>Growing Good Since 1906</span></div>
</section>

<section class="slide" style="left:924px;top:1066px">
  <div class="logo"><i></i>Lakeshore Grain</div>
  <div class="abs blue" style="left:85px;top:5px;width:100px;height:100px"></div>
  <div class="ph beets" role="img" aria-label="Large pile of harvested beets" style="left:76px;top:9px;width:100px;height:92px"></div>
  <div class="title inline" style="left:13px;top:28px;font-size:6.2px;color:var(--navy)">Contact <b>Us</b></div>
  <div class="abs body sm" style="left:13px;top:38px;width:58px">We are glad to help with any question.</div>
  <svg class="abs" style="left:13px;top:49px" width="6" height="40" viewBox="0 0 6 40">
    <g fill="none" stroke="#2b4ba3" stroke-width=".4"><circle cx="3" cy="3" r="2.6"/><circle cx="3" cy="19" r="2.6"/><circle cx="3" cy="35" r="2.6"/></g>
    <path d="M2 2 L2.6 1.6 L3.2 2.6 L2.8 3 Q3.2 3.8 3.8 4 L4.2 3.6 L4.8 4.2 L4.4 4.6 Q2.2 4.4 2 2 Z" fill="#2b4ba3"/>
    <path d="M1.6 18 L4.4 18 M3 16.6 L3 21.4 M1.6 20 L4.4 20" stroke="#2b4ba3" stroke-width=".3"/>
    <rect x="1.6" y="34" width="2.8" height="2" fill="none" stroke="#d7263d" stroke-width=".3"/>
  </svg>
  <div class="abs body sm" style="left:22px;top:48.5px;line-height:1.3"><strong style="font-size:2.4px">Phone</strong><br>555-0100-2468</div>
  <div class="abs body sm" style="left:22px;top:64.5px;line-height:1.3"><strong style="font-size:2.4px">Web Address</strong><br>www.lakeshoregrain.com</div>
  <div class="abs body sm" style="left:22px;top:80.5px;line-height:1.3"><strong style="font-size:2.4px">Email Address</strong><br>info@lakeshoregrain.com</div>
</section>

</div>
</body>
</html>
```